Satchel & Sundial needs new business card design

I need a new business card design. I'm looking for out-of-the-box design which represents the freedom of being a location independent entrepreneur.
I offer coaching, retreats and trips.
I would like to see designs with and without the photo.
Colors I use are black (#000000), green (#25A796) and brown (#D7C38C)
Website satchelandsundial.example

Target Market(s)

location independent entrepreneurs, digital nomads, people looking to swap the 9 to 5 for a lifestyle business

Industry/Entity Type

Business

Contact Information for Business Card

Dorota Falkner
Your Lifestyle Business Coach, Retreat & Trip Leader
http://satchelandsundial.example
hello@satchelandsundial.example
Live a life you don't need a holiday from

Font styles to use
Serif
Sans Serif

Requirements
Must have
• One side should contain only the logo. I would also consider having the "Live a life you don't need a holiday from" on that side too (depending on how it looks)
• Please show both sides on the designs.

```html
<!DOCTYPE html>
<html lang="en">
<head>
<meta charset="utf-8">
<title>Satchel &amp; Sundial business card</title>
<link rel="stylesheet" href="https://fonts.googleapis.com/css2?family=Arimo:wght@400;700&display=swap">
<style>
  :root {
    --ink: #1e1e1e;
    --name-grey: #3a3a3a;
    --brand-green: #25a796;
    --stage: #e9e6e0;
    --card: #ffffff;
    --arc: #333333;
    --photo-leaf: #5f8a4a;
    --photo-light: #c9d6b0;
    --photo-earth: #8a7a5a;
  }
  * { margin: 0; padding: 0; box-sizing: border-box; }
  html, body { width: 1200px; height: 892px; overflow: hidden; }
  body {
    background: var(--stage);
    font-family: "Arimo", Arial, sans-serif;
    color: var(--ink);
    position: relative;
  }
  .card {
    position: absolute;
    width: 620px;
    height: 354px;
    background: var(--card);
    box-shadow: 0 6px 18px rgba(0,0,0,0.18);
    overflow: hidden;
  }
  .card--back { left: 520px; top: 60px; }
  .card--front { left: 70px; top: 470px; }

  .wordmark {
    font-weight: 700;
    text-transform: uppercase;
    color: var(--ink);
    letter-spacing: 1px;
    white-space: nowrap;
  }
  .card--back .wordmark {
    position: absolute;
    left: 0; right: 0; top: 110px;
    text-align: center;
    font-size: 44px;
  }
  .tagline {
    position: absolute;
    left: 0; right: 0; top: 250px;
    text-align: center;
    font-size: 19px;
  }

  .photo-panel { position: absolute; left: 0; top: 0; width: 620px; height: 354px; }
  .card--front .wordmark {
    position: absolute;
    right: 24px; top: 50px;
    font-size: 22px;
    letter-spacing: 0.5px;
    text-align: right;
  }
  .holder {
    position: absolute;
    left: 322px; top: 118px;
  }
  .holder__name {
    font-weight: 700;
    font-size: 26px;
    color: var(--name-grey);
  }
  .holder__role {
    margin-top: 4px;
    font-size: 17px;
    line-height: 1.2;
    color: var(--brand-green);
  }
  .contacts {
    position: absolute;
    left: 270px; top: 262px;
    list-style: none;
    font-size: 17px;
  }
  .contacts li { display: flex; align-items: center; gap: 12px; margin-bottom: 8px; }
  .contacts svg { width: 18px; height: 18px; flex: none; }
</style>
</head>
<body>
  <section class="card card--back" aria-label="Card back">
    <div class="wordmark">Satchel &amp; Sundial</div>
    <p class="tagline">Live a life you don't need a holiday from</p>
  </section>

  <section class="card card--front" aria-label="Card front">
    <svg class="photo-panel" viewBox="0 0 620 354" role="img" aria-label="Photo of the coach sitting on a wooden fence among green trees, holding a small sign">
      <defs>
        <linearGradient id="foliage" x1="0" y1="0" x2="0.6" y2="1">
          <stop offset="0" stop-color="var(--photo-light)"/>
          <stop offset="0.45" stop-color="var(--photo-leaf)"/>
          <stop offset="1" stop-color="var(--photo-earth)"/>
        </linearGradient>
      </defs>
      <path d="M0 0 H360 Q250 230 150 354 H0 Z" fill="url(#foliage)"/>
      <path d="M360 0 Q250 230 150 354" fill="none" stroke="var(--arc)" stroke-width="7"/>
    </svg>
    <div class="wordmark">Satchel &amp; Sundial</div>
    <div class="holder">
      <p class="holder__name">Dorota Falkner</p>
      <p class="holder__role">Your Lifestyle Business Coach,<br>Retreat &amp; Trip Leader</p>
    </div>
    <ul class="contacts">
      <li>
        <svg viewBox="0 0 18 18" aria-hidden="true"><rect width="18" height="18" fill="var(--ink)"/><rect x="3" y="5" width="12" height="8" fill="none" stroke="#fff" stroke-width="1.4"/><path d="M3 5 L9 10 L15 5" fill="none" stroke="#fff" stroke-width="1.4"/></svg>
        <span>hello@satchelandsundial.example</span>
      </li>
      <li>
        <svg viewBox="0 0 18 18" aria-hidden="true"><rect width="18" height="18" fill="var(--ink)"/><circle cx="9" cy="9" r="5.5" fill="none" stroke="#fff" stroke-width="1.4"/><path d="M3.5 9 H14.5 M9 3.5 Q5.5 9 9 14.5 Q12.5 9 9 3.5" fill="none" stroke="#fff" stroke-width="1.2"/></svg>
        <span>http://satchelandsundial.example</span>
      </li>
    </ul>
  </section>
</body>
</html>
```